Irrigation Business needs their business cards modernised and revamped

I would like to keep my current logo, colours and revamp the format of the card.

I would like the card to be clean yet important.

Im not sure if you include texture but i would like the named logo to be indented into the card etc.

show me something alive and free something thats clinical to the point yet has a feel of achievement. i would like people to go nice card.

Target Market(s)

high end clients, corporate, sports field manger, the guys that make the decisions

Industry/Entity Type

Business

Contact Information for Business Card

nformation to be included

Dean Harlow (Director)
0487305526
dean@kolvat.biz
www.kestonfieldworks.com

instagram logo
google logo
facebook logo

Colors

Designer to choose colors to be used in the design.

Requirements
Nice to have
• indentations a really nice feel to the card good texture

```html
<!DOCTYPE html>
<html lang="en">
<head>
<meta charset="utf-8">
<title>Keston Fieldworks – Business Card</title>
<link rel="stylesheet" href="https://fonts.googleapis.com/css2?family=Open+Sans:wght@400;600;700;800&display=swap">
<style>
  :root {
    --stage: #e9e9eb;
    --brand-blue: #2f66ae;
    --brand-sky: #2ea8dc;
    --card-white: #f2f2f2;
    --ink-white: #ffffff;
    --icon-fill: #e6eef8;
  }
  * { margin: 0; padding: 0; box-sizing: border-box; }
  html, body { width: 1200px; height: 900px; overflow: hidden; }
  body {
    position: relative;
    background: var(--stage);
    font-family: "Open Sans", Arial, sans-serif;
  }
  .card {
    position: absolute;
    box-shadow: 0 6px 18px rgba(0,0,0,0.18);
    overflow: hidden;
  }

  /* Contact side */
  .card--contact {
    left: 78px; top: 35px; width: 587px; height: 363px;
    background: var(--brand-blue);
    color: var(--ink-white);
  }
  .contact__emblem {
    position: absolute; left: 9px; top: 7px;
    width: 336px; height: 336px; border-radius: 50%;
    border: 10px solid var(--brand-sky);
    display: flex; flex-direction: column; align-items: center; justify-content: center;
    color: var(--brand-sky);
    font-weight: 800; font-size: 40px; line-height: 1.05; letter-spacing: 0.5px;
    text-align: center;
  }
  .contact__identity {
    position: absolute; right: 23px; top: 44px; text-align: right;
  }
  .contact__name {
    font-weight: 700; font-size: 21px; letter-spacing: 0.2px; line-height: 1.1;
  }
  .contact__role {
    font-weight: 400; font-size: 15px; line-height: 1.2;
  }
  .contact__social {
    position: absolute; right: 24px; top: 240px;
    display: flex; gap: 6px;
  }
  .social-link {
    width: 23px; height: 23px; border-radius: 50%;
    background: var(--icon-fill);
    display: inline-flex; align-items: center; justify-content: center;
  }
  .contact__lines {
    position: absolute; right: 24px; top: 277px;
    list-style: none; text-align: right;
    font-size: 15px; line-height: 24px;
  }
  .contact__lines li {
    display: flex; justify-content: flex-end; align-items: center; gap: 6px;
  }
  .contact__icon {
    width: 17px; height: 17px; border-radius: 50%;
    background: var(--icon-fill);
    display: inline-flex; align-items: center; justify-content: center;
  }

  /* Brand side */
  .card--brand {
    left: 388px; top: 505px; width: 567px; height: 352px;
    background: var(--card-white);
  }
  .brand__mark {
    position: absolute; left: 222px; top: 76px;
    width: 124px; height: 124px; border-radius: 50%;
    background: var(--brand-blue);
  }
  .brand__name {
    position: absolute; left: 0; right: 0; top: 212px;
    text-align: center;
    font-weight: 700; font-size: 34px; line-height: 38px; letter-spacing: -0.3px;
    color: var(--brand-blue);
  }
  .brand__name span {
    display: block;
    font-size: 24px; line-height: 30px; letter-spacing: 7px;
  }
  .brand__web {
    position: absolute; left: 0; right: 0; top: 296px;
    text-align: center;
    font-weight: 600; font-size: 15px;
    color: var(--brand-blue);
  }
</style>
</head>
<body>
  <section class="card card--contact" aria-label="Business card, contact side">
    <div class="contact__emblem">
      <span>KESTON</span>
      <span>FIELD</span>
      <span>WORKS</span>
    </div>
    <div class="contact__identity">
      <p class="contact__name">DEAN HARLOW</p>
      <p class="contact__role">Director</p>
    </div>
    <div class="contact__social" aria-label="Social links">
      <span class="social-link">
        <svg width="12" height="12" viewBox="0 0 24 24" aria-hidden="true"><path d="M5 12h13M13 6l6 6-6 6" fill="none" stroke="var(--brand-blue)" stroke-width="3" stroke-linecap="round" stroke-linejoin="round"/></svg>
      </span>
      <span class="social-link">
        <svg width="12" height="12" viewBox="0 0 24 24" aria-hidden="true"><path d="M5 12h13M13 6l6 6-6 6" fill="none" stroke="var(--brand-blue)" stroke-width="3" stroke-linecap="round" stroke-linejoin="round"/></svg>
      </span>
      <span class="social-link">
        <svg width="12" height="12" viewBox="0 0 24 24" aria-hidden="true"><path d="M5 12h13M13 6l6 6-6 6" fill="none" stroke="var(--brand-blue)" stroke-width="3" stroke-linecap="round" stroke-linejoin="round"/></svg>
      </span>
    </div>
    <ul class="contact__lines">
      <li>0487305526
        <span class="contact__icon">
          <svg width="11" height="11" viewBox="0 0 24 24" aria-hidden="true"><path fill="var(--brand-blue)" d="M6.6 10.8a15.1 15.1 0 0 0 6.6 6.6l2.2-2.2c.3-.3.7-.4 1-.2 1.1.4 2.3.6 3.6.6.6 0 1 .4 1 1V20c0 .6-.4 1-1 1A17 17 0 0 1 3 4c0-.6.4-1 1-1h3.5c.6 0 1 .4 1 1 0 1.3.2 2.5.6 3.6.1.3 0 .7-.2 1z"/></svg>
        </span>
      </li>
      <li>dean@kolvat.biz
        <span class="contact__icon">
          <svg width="11" height="11" viewBox="0 0 24 24" aria-hidden="true"><rect x="2" y="5" width="20" height="14" rx="2" fill="var(--brand-blue)"/><path d="M3 6l9 7 9-7" fill="none" stroke="var(--icon-fill)" stroke-width="2"/></svg>
        </span>
      </li>
    </ul>
  </section>

  <section class="card card--brand" aria-label="Business card, brand side">
    <span class="brand__mark"></span>
    <p class="brand__name">KESTON<span>FIELDWORKS</span></p>
    <p class="brand__web">www.kestonfieldworks.com</p>
  </section>
</body>
</html>
```